Wine label for family vineyard start-up

Brand new family vineyard needs a new label:

The information we need on the label is the following:
- Merlot & Cabernet (variety)
- Ponte Capriasca (location)
- 2016 (vintage)

The style of the label should be graphic / minimal / masculine.

This is a wine made by three 35yr old guys

Target Market(s)

young & urban

Industry/Entity Type

Vineyard

Logo Text

Merlot & Cabernet / Ponte Capriasca / 2016

Font styles to use
Sans Serif

Requirements
Must have
• clearly legible
• aesthetically pleasing [minimalist]
• sans serif

```html
<!DOCTYPE html>
<html lang="en">
<head>
<meta charset="UTF-8">
<title>Merlot &amp; Cabernet — Ponte Capriasca 2016</title>
<link rel="stylesheet" href="https://fonts.googleapis.com/css2?family=Josefin+Sans:wght@700&display=swap">
<style>
  :root {
    --wine-centre: #7a1f25;
    --wine-edge: #571d22;
    --label-black: #1e1d1b;
    --mark-tone: #3b3a37;
    --ink-white: #ffffff;
  }
  html, body {
    margin: 0;
    padding: 0;
    width: 1200px;
    height: 1200px;
    overflow: hidden;
  }
  .canvas {
    position: relative;
    width: 1200px;
    height: 1200px;
    background: radial-gradient(circle at 50% 50%, var(--wine-centre) 0%, var(--wine-edge) 75%);
  }
  .wine-label {
    position: absolute;
    left: 400px;
    top: 282px;
    width: 374px;
    height: 638px;
    background: var(--label-black);
  }
  .mark-area {
    position: absolute;
    left: 62px;
    top: 134px;
    width: 250px;
    height: 240px;
    background: var(--mark-tone);
  }
  .label-text {
    position: absolute;
    left: 0;
    width: 100%;
    margin: 0;
    text-align: center;
    font-family: "Josefin Sans", sans-serif;
    font-weight: 700;
    font-size: 30px;
    color: var(--ink-white);
    text-transform: uppercase;
    line-height: 1;
  }
  .variety {
    top: 490px;
    letter-spacing: -0.2px;
  }
  .location {
    top: 524px;
    letter-spacing: -0.2px;
  }
  .vintage {
    top: 588px;
  }
</style>
</head>
<body>
  <main class="canvas">
    <section class="wine-label">
      <div class="mark-area" role="img" aria-label="Brushed white open ring symbol of the vineyard"></div>
      <p class="label-text variety">Merlot &amp; Cabarnet</p>
      <p class="label-text location">Ponte Capriasca</p>
      <p class="label-text vintage">2016</p>
    </section>
  </main>
</body>
</html>
```